Creation of a page for funnel

Our company is specialized in insoles and well-being. Our insoles help reduce joint problems, stress or ink to promote weight loss. We need a clean and refined sales page, this one will be used on funnel click. The page should display the values of our product in first: "promote weight loss" in second: "Relieves muscle and joint pain" third: "Increases energy and stress stress". The page must be in the colors of our logo (green) if possible this color: light green: dark green 54c248. It is important to follow this model for the page with totally new and fresh desing: https: // lunar-pebble. uk / qtw-lr Additionnal details for icons Section u: 1: "A unique design based on two types of knowledge" 2: "approved by acupressure expert" "Lose weight" 2: "Increases blood flow and oxygen in your body" 3: "Relieves muscle and joint pain" 4: "Increases energy and reduces stress" Section x: 1: "for men and women" 2: "one size "3:" Adjustable by cutting "Section y: 1:" powerful magnet in tourmaline "2:" for all type of shoes "3:" Flexible and light "4:" Breathable "Section z: 1:" free shipping "2 : "Customer service" 3: "money back guarantee" 4: "safe payment"
Target Market(s)
men and women 35
Number of Pages Required
1 page
Requirements
Must have
- the 5 sections mentioned in description
Nice to have
- some GIF like the funnel

```html
<!DOCTYPE html>
<html lang="en">
<head>
<meta charset="utf-8">
<title>StrideLeaf – Comfort insoles</title>
<link href="https://fonts.googleapis.com/css2?family=Montserrat:wght@600;700;800&family=Roboto:wght@400;500;700&display=swap" rel="stylesheet">
<style>
:root{
  --green:#54c248;
  --green-dark:#3aa935;
  --green-pale:#e6f9e4;
  --ink:#222222;
  --text:#333333;
  --muted:#6b6b6b;
  --charcoal:#3a3a3a;
  --white:#ffffff;
}
*{margin:0;padding:0;box-sizing:border-box}
html,body{width:1200px;height:4441px;overflow:hidden}
body{position:relative;background:var(--white);font-family:"Roboto",Arial,sans-serif;color:var(--text)}
.abs{position:absolute}
.display{font-family:"Montserrat",Arial,sans-serif;font-weight:800}
.accent{color:var(--green)}
.btn{position:absolute;display:flex;align-items:center;justify-content:center;gap:8px;background:var(--green);color:var(--white);font-family:"Montserrat",Arial,sans-serif;font-weight:700;font-size:15px;text-transform:uppercase;border:2px solid var(--green-dark)}
/* header */
.topline{left:0;top:0;width:1200px;height:4px;background:var(--green)}
.header{left:0;top:4px;width:1200px;height:106px;background:var(--white)}
.brand{display:flex;align-items:center;gap:10px}
.brand-dot{width:36px;height:36px;border-radius:50%;background:var(--green)}
.brand-name{font-family:"Montserrat",Arial,sans-serif;font-weight:600;font-size:38px;color:var(--charcoal);line-height:1}
.brand-tag{font-size:17px;color:var(--text);margin-top:2px}
.nav{left:505px;top:42px;display:flex;gap:30px;font-size:17px;color:var(--text)}
/* hero */
.hero-photo{left:0;top:110px;width:1200px;height:680px;background:linear-gradient(100deg,#8a8a8a 0%,#b9b9b9 45%,#d9d9d9 100%)}
.hero-title{left:141px;top:300px;font-size:70px;line-height:70px;color:var(--white)}
.hero-sub{left:144px;top:470px;font-size:19px;color:var(--white)}
.dots{left:143px;top:676px;display:flex;gap:12px}
.dots span{width:12px;height:12px;border-radius:50%;background:var(--white)}
.dots span.on{background:var(--green)}
/* solutions */
.fade-photo{background:linear-gradient(180deg,#ffffff 0%,#eeeeee 60%,#f6f6f6 100%)}
.side-word{font-family:"Montserrat",Arial,sans-serif;font-weight:800;font-size:66px;color:#e4e4e4;transform:rotate(-90deg);transform-origin:left top;letter-spacing:2px}
.sec-title{left:0;width:1200px;text-align:center;font-size:50px;line-height:54px;color:var(--ink);font-family:"Montserrat",Arial,sans-serif;font-weight:700}
.sec-lead{left:0;width:1200px;text-align:center;font-size:20px;line-height:33px;color:var(--text)}
.label{font-size:19px;line-height:26px;color:var(--ink)}
.placeholder{border-radius:4px}
/* benefits */
.benefit h3{font-family:"Roboto",Arial,sans-serif;font-weight:500;font-size:17px;line-height:21px;color:var(--ink)}
.benefit p{font-size:13px;line-height:26px;color:var(--muted);margin-top:8px}
.benefit.right-align{text-align:right}
.ghost{font-family:"Montserrat",Arial,sans-serif;font-weight:800;color:rgba(84,194,72,.12)}
/* badges */
.badge{position:absolute;border-radius:50%;background:#3c3c3c;border:12px solid var(--green);display:flex;flex-direction:column;align-items:center;justify-content:center;color:var(--white);font-family:"Montserrat",Arial,sans-serif;font-weight:700;text-align:center}
/* features */
.feature{display:flex;gap:30px;width:480px}
.feature .ficon{flex:none;width:104px;height:104px}
.feature h3{font-weight:500;font-size:17px;color:var(--ink);margin-top:10px}
.feature p{font-size:13px;line-height:26px;color:var(--muted);margin-top:12px}
/* services */
.card{position:absolute;width:262px;height:154px;background:var(--white);border-radius:4px;box-shadow:0 6px 18px rgba(0,0,0,.15);padding:26px 20px 0 72px}
.card svg{position:absolute;left:20px;top:26px}
.card h3{font-weight:500;font-size:19px;color:var(--ink);line-height:22px}
.card p{font-size:12px;line-height:24px;color:var(--muted);margin-top:6px}
/* footer */
.foot-head{font-size:18px;color:var(--charcoal)}
.foot-list{list-style:none;font-size:13px;color:var(--muted);line-height:24px;margin-top:22px}
.foot-list li::before{content:"»";color:var(--green);margin-right:12px}
.contact-row{display:flex;gap:16px;font-size:13px;line-height:21px;color:var(--muted)}
.social{display:flex;gap:8px}
.social span{width:30px;height:30px;border-radius:50%}
.copyright{left:0;width:1200px;top:4398px;text-align:center;font-size:13px;color:var(--muted)}
</style>
</head>
<body>

<!-- Header -->
<div class="abs topline"></div>
<header class="abs header">
  <div class="abs brand" style="left:143px;top:20px">
    <span class="brand-dot"></span>
    <div>
      <div class="brand-name">StrideLeaf</div>
      <div class="brand-tag">Un pas vers le confort !</div>
    </div>
  </div>
  <nav class="abs nav"><span>Home</span><span>How It Works</span><span>Pricing</span><span>FAQ</span><span>Contact us</span></nav>
  <div class="btn" style="left:957px;top:32px;width:98px;height:40px;font-size:12px">Shop now</div>
</header>

<!-- Hero -->
<div class="abs hero-photo" role="img" aria-label="Photo of a person fitting an insole into a shoe"></div>
<h1 class="abs display hero-title">Relieve <span class="accent">Pain,</span><br>Lose weight</h1>
<p class="abs hero-sub">Lorem ipsum dolor sit amet consectetur adipiscing elitore</p>
<div class="btn" style="left:145px;top:538px;width:152px;height:38px">Shop now
  <svg width="14" height="14" viewBox="0 0 14 14"><circle cx="7" cy="7" r="7" fill="#fff"/><path d="M5 4l3 3-3 3" stroke="#54c248" stroke-width="2" fill="none"/></svg></div>
<div class="abs dots"><span></span><span></span><span class="on"></span><span></span><span></span></div>
<svg class="abs" style="left:0;top:690px" width="1200" height="110" viewBox="0 0 1200 110">
  <path d="M0 60 C300 130 700 -20 1200 60 L1200 110 L0 110Z" fill="#fff"/>
  <path d="M0 60 C300 120 700 -20 1200 60 L1200 80 C700 10 300 140 0 90Z" fill="#54c248"/>
</svg>

<!-- Solutions -->
<div class="abs fade-photo" style="left:0;top:790px;width:1200px;height:920px" role="img" aria-label="Soft faded photo of an insole on a light background"></div>
<div class="abs side-word" style="left:72px;top:1318px">SOLUTIONS</div>
<h2 class="abs sec-title" style="top:884px">A totally natural solution<br><span class="accent">without any health risk</span></h2>
<p class="abs sec-lead" style="top:1016px">Approved by acupressure expert<br>A unique design based on two types of knowledge</p>
<div class="abs placeholder" style="left:379px;top:1112px;width:388px;height:336px;background:radial-gradient(ellipse at center,#54c248 0%,#6d7478 45%,#e8e8e8 75%,transparent 76%)" role="img" aria-label="Illustration of three stacked insole layers"></div>
<div class="abs label" style="left:784px;top:1180px">Increases energy and<br>reduces stress</div>
<div class="abs label" style="left:170px;top:1285px;width:239px;text-align:right">Relieves muscle and<br>joint pain</div>
<div class="abs label" style="left:686px;top:1384px">Promote weight loss</div>
<div class="abs placeholder" style="left:445px;top:1453px;width:124px;height:116px;background:linear-gradient(135deg,#1e1e1e,#3d3d3d 60%,#d8d03a)" role="img" aria-label="Photo of a pair of black insoles"></div>
<div class="btn" style="left:603px;top:1491px;width:154px;height:43px">Shop now!</div>

<!-- Adapted -->
<svg class="abs" style="left:0;top:1660px" width="1200" height="110" viewBox="0 0 1200 110">
  <path d="M0 20 C250 110 700 100 1200 40 L1200 110 L0 110Z" fill="#e6f9e4"/>
  <path d="M0 20 C250 110 700 100 1200 40 L1200 46 C700 80 300 100 0 44Z" fill="#54c248"/>
</svg>
<div class="abs" style="left:0;top:1770px;width:1200px;height:800px;background:var(--green-pale)"></div>
<div class="abs ghost" style="left:831px;top:1818px;font-size:62px">ADAPTED</div>
<h2 class="abs sec-title" style="top:1814px">Adapted To Your<br><span class="accent">Daily Life!</span></h2>
<div class="abs placeholder" style="left:465px;top:1974px;width:276px;height:371px;background:radial-gradient(ellipse at center,#54c248 0%,#3aa935 50%,transparent 72%)" role="img" aria-label="Illustration of two green footprints made of leaves"></div>

<div class="abs benefit right-align" style="left:150px;top:2006px;width:217px">
  <h3>Lose weight</h3>
  <p>Lorem ipsum dolor sit amet, con-<br>sectetur adipiscing elit, sed do<br>eiusmod tempor incididunt</p>
</div>
<svg class="abs" style="left:383px;top:1996px" width="44" height="44" viewBox="0 0 44 44" fill="none" stroke="#54c248" stroke-width="2"><rect x="4" y="4" width="36" height="36" rx="6"/><circle cx="22" cy="18" r="8"/><path d="M22 18l3-4"/></svg>
<div class="abs benefit right-align" style="left:120px;top:2192px;width:247px">
  <h3>Increases blood flow<br>and oxygen throughout<br>your body</h3>
  <p>Lorem ipsum dolor sit amet, conei-<br>usmod tempor incididunt</p>
</div>
<svg class="abs" style="left:383px;top:2192px" width="44" height="56" viewBox="0 0 44 56" fill="none" stroke="#54c248" stroke-width="2"><circle cx="22" cy="12" r="6"/><path d="M14 26h16v14h-4v12h-8V40h-4z"/><path d="M4 4h6M34 4h6M4 52h6M34 52h6"/></svg>
<svg class="abs" style="left:764px;top:1996px" width="54" height="48" viewBox="0 0 54 48" fill="none" stroke="#54c248" stroke-width="2"><path d="M4 4l8 30h30"/><circle cx="30" cy="22" r="10"/><path d="M30 16l-3 7h6l-3 7"/></svg>
<div class="abs benefit" style="left:834px;top:2006px;width:230px">
  <h3>Relieves muscle and<br>joint pain</h3>
  <p>Lorem ipsum dolor sit amet, con-<br>sectetur adipiscing elit, sed do<br>eiusmod tempor incididunt</p>
</div>
<svg class="abs" style="left:768px;top:2180px" width="48" height="58" viewBox="0 0 48 58" fill="none" stroke="#54c248" stroke-width="2"><circle cx="24" cy="26" r="7"/><path d="M10 56v-8c0-8 6-12 14-12s14 4 14 12v8z"/><path d="M8 4l4 8-4 0 4 8M40 4l-4 8 4 0-4 8"/></svg>
<div class="abs benefit" style="left:834px;top:2192px;width:230px">
  <h3>Increases energy and<br>reduces stress</h3>
  <p>Lorem ipsum dolor sit amet, con-<br>sectetur adipiscing elit, sed do<br>eiusmod tempor incididunt</p>
</div>
<div class="btn" style="left:496px;top:2390px;width:209px;height:46px;background:var(--charcoal);border-color:#2b2b2b">Shop now!</div>

<!-- Badges -->
<div class="abs fade-photo" style="left:0;top:2570px;width:1200px;height:900px" role="img" aria-label="Soft faded photo of a foot on an insole"></div>
<svg class="abs" style="left:0;top:2520px" width="1200" height="200" viewBox="0 0 1200 200">
  <path d="M0 0H1200V40C900 110 400 90 0 150Z" fill="#e6f9e4"/>
  <path d="M900 140L1200 80V160L900 200Z" fill="#54c248"/>
</svg>
<div class="badge" style="left:165px;top:2560px;width:276px;height:276px;font-size:24px">
  <svg width="84" height="84" viewBox="0 0 84 84" fill="none" stroke="#fff" stroke-width="3"><ellipse cx="28" cy="36" rx="12" ry="24"/><ellipse cx="56" cy="36" rx="12" ry="24"/><path d="M24 66h8M52 66h8"/></svg>
  <div style="margin-top:10px;line-height:30px">For Men &amp;<br>Women</div>
</div>
<div class="badge" style="left:430px;top:2526px;width:344px;height:344px;font-size:32px;border-width:18px;border-color:#7ccf73;box-shadow:inset 0 0 0 6px #54c248">
  <svg width="110" height="80" viewBox="0 0 110 80" fill="none" stroke="#fff" stroke-width="3"><path d="M20 10v40c0 10 10 16 30 16h40c10 0 10-14 0-16L50 40V10z"/><path d="M10 74h90"/></svg>
  <div style="margin-top:20px">One size</div>
</div>
<div class="badge" style="left:759px;top:2560px;width:276px;height:276px;font-size:24px">
  <svg width="84" height="84" viewBox="0 0 84 84" fill="none" stroke="#fff" stroke-width="3"><ellipse cx="28" cy="40" rx="12" ry="24"/><ellipse cx="56" cy="36" rx="12" ry="24"/><ellipse cx="28" cy="40" rx="6" ry="14"/><ellipse cx="56" cy="36" rx="6" ry="14"/></svg>
  <div style="margin-top:10px;line-height:30px">Adjustable by<br>cutting</div>
</div>

<!-- Features -->
<div class="abs side-word" style="left:72px;top:3422px">FEATURES</div>
<h2 class="abs sec-title" style="top:2988px">Specific <span class="accent">Features</span></h2>
<div class="abs feature" style="left:181px;top:3120px">
  <svg class="ficon" viewBox="0 0 104 104" fill="none" stroke="#54c248" stroke-width="2"><path d="M8 30c20 0 30 14 30 36C18 62 8 50 8 30z" fill="#54c248"/><circle cx="62" cy="62" r="34"/><path d="M56 50l8 8-4 4 8 8"/></svg>
  <div><h3>Powerful magnet in tourmaline</h3><p>Lorem ipsum dolor sit amet, consectetur<br>adipiscusmod tempor incididunt</p></div>
</div>
<div class="abs feature" style="left:638px;top:3120px">
  <svg class="ficon" viewBox="0 0 104 104" fill="none" stroke="#54c248" stroke-width="2"><path d="M8 30c20 0 30 14 30 36C18 62 8 50 8 30z" fill="#54c248"/><circle cx="62" cy="62" r="34"/><path d="M50 80c0-14 24-20 24-34"/></svg>
  <div><h3>For all type of shoes</h3><p>Lorem ipsum dolor sit amet, consectetur<br>adipiscusmod tempor incididunt</p></div>
</div>
<div class="abs feature" style="left:181px;top:3277px">
  <svg class="ficon" viewBox="0 0 104 104" fill="none" stroke="#54c248" stroke-width="2"><path d="M8 30c20 0 30 14 30 36C18 62 8 50 8 30z" fill="#54c248"/><circle cx="62" cy="62" r="34"/><circle cx="62" cy="62" r="10"/><path d="M56 62l5 5 8-9"/></svg>
  <div><h3>Flexible and light</h3><p>Lorem ipsum dolor sit amet, consectetur<br>adipiscusmod tempor incididunt</p></div>
</div>
<div class="abs feature" style="left:638px;top:3277px">
  <svg class="ficon" viewBox="0 0 104 104" fill="none" stroke="#54c248" stroke-width="2"><path d="M8 30c20 0 30 14 30 36C18 62 8 50 8 30z" fill="#54c248"/><circle cx="62" cy="62" r="34"/><path d="M52 54a10 10 0 1 1 10 12v6"/></svg>
  <div><h3>Breathable</h3><p>Lorem ipsum dolor sit amet, consectetur<br>adipiscusmod tempor incididunt</p></div>
</div>

<!-- Services -->
<svg class="abs" style="left:0;top:3450px" width="1200" height="620" viewBox="0 0 1200 620">
  <path d="M0 30C300 110 700 -20 1200 50V580C800 620 300 520 0 600Z" fill="#54c248"/>
  <path d="M0 30C300 110 700 -20 1200 50V60C700 0 300 120 0 56Z" fill="#333"/>
  <path d="M0 600C300 520 800 620 1200 580V620H0Z" fill="#fff"/>
</svg>
<div class="abs" style="left:0;top:3520px;width:1200px;height:520px;background:linear-gradient(180deg,rgba(58,169,53,0) 0%,rgba(40,120,40,.25) 100%)" role="img" aria-label="Faded photo of a runner on a grass track"></div>
<div class="abs display" style="left:638px;top:3566px;font-size:62px;color:rgba(255,255,255,.3)">FREE SHIPPING</div>
<div class="card" style="left:145px;top:3703px">
  <svg width="40" height="30" viewBox="0 0 40 30" fill="#54c248"><rect x="0" y="4" width="24" height="18"/><path d="M24 10h9l6 7v5H24z"/><circle cx="8" cy="25" r="4"/><circle cx="31" cy="25" r="4"/></svg>
  <h3>Free shipping</h3><p>Lorem ipsum dolor sit an<br>consectetur adipiscusmo.<br>tempor incididunt</p>
</div>
<div class="card" style="left:360px;top:3646px">
  <svg width="36" height="32" viewBox="0 0 36 32" fill="none" stroke="#54c248" stroke-width="4"><path d="M4 26V18a14 14 0 0 1 28 0v8"/><rect x="2" y="20" width="6" height="10" fill="#54c248"/><rect x="28" y="20" width="6" height="10" fill="#54c248"/></svg>
  <h3>customer service</h3><p>Lorem ipsum dolor sit amet,<br>consectetur adipiscusmod<br>tempor incididunt</p>
</div>
<div class="card" style="left:579px;top:3758px">
  <svg width="36" height="36" viewBox="0 0 36 36" fill="none" stroke="#54c248" stroke-width="4"><path d="M6 18a12 12 0 1 0 4-9"/><path d="M4 4v8h8"/><path d="M18 10v9l6 4"/></svg>
  <h3>Money back<br>guarantee</h3><p>Lorem ipsum dolor sit<br>amet, consectetudidunt</p>
</div>
<div class="card" style="left:793px;top:3703px">
  <svg width="32" height="36" viewBox="0 0 32 36" fill="none" stroke="#54c248" stroke-width="4"><path d="M16 2L3 7v10c0 9 6 15 13 17 7-2 13-8 13-17V7z"/><path d="M16 6v24" /></svg>
  <h3>Safe payment</h3><p>Lorem ipsum dolor sit amet,<br>consectetur adipiscusmod<br>tempor incididunt</p>
</div>

<!-- Footer -->
<div class="abs" style="left:0;top:4070px;width:1200px;height:371px;background:linear-gradient(180deg,#ffffff 0%,#f1f1f1 70%,#e6e6e6 100%)" role="img" aria-label="Soft faded photo of insoles"></div>
<div class="abs brand" style="left:178px;top:4160px">
  <span class="brand-dot"></span>
  <div>
    <div class="brand-name" style="font-size:44px">StrideLeaf</div>
    <div class="brand-tag">Un pas vers le confort !</div>
  </div>
</div>
<div class="abs social" style="left:178px;top:4254px"><span style="background:#2b3f8c"></span><span style="background:#2a9bd8"></span><span style="background:#d33a2c"></span><span style="background:#8b6a2b"></span></div>
<div class="abs" style="left:593px;top:4152px">
  <div class="foot-head">QUICK LINKS</div>
  <ul class="foot-list"><li>Home</li><li>About</li><li>How It Works</li><li>Pricing</li><li>FAQ</li></ul>
</div>
<div class="abs" style="left:793px;top:4152px">
  <div class="foot-head">CONTACT INFO</div>
  <div class="contact-row" style="margin-top:22px">
    <svg width="16" height="22" viewBox="0 0 16 22"><path d="M8 0a8 8 0 0 1 8 8c0 6-8 14-8 14S0 14 0 8a8 8 0 0 1 8-8z" fill="#54c248"/><circle cx="8" cy="8" r="3" fill="#fff"/></svg>
    <span>122,Lorem ipsum dolor sit amet<br>sed do eiusmod..</span></div>
  <div class="contact-row" style="margin-top:14px">
    <svg width="16" height="16" viewBox="0 0 16 16"><path d="M3 0l3 4-2 2c1 3 3 5 6 6l2-2 4 3-2 3C7 16 0 9 0 3z" fill="#54c248"/></svg>
    <span>Phone : 1 800 555 0142</span></div>
  <div class="contact-row" style="margin-top:14px">
    <svg width="18" height="14" viewBox="0 0 18 14"><rect width="18" height="14" fill="#54c248"/><path d="M0 0l9 7 9-7" stroke="#fff" stroke-width="1.5" fill="none"/></svg>
    <span>hello@strideleaf.example</span></div>
</div>
<p class="abs copyright">Copyrights © 2019, StrideLeaf Ltd. All rights reserved &nbsp;|&nbsp; Privacy Policy &nbsp;|&nbsp; Terms of use</p>

</body>
</html>
```